KBT Business Cards

We require business cards for our business. We would like a matte black back to the card, with our logo centred in the middle. The front side of the card is open to design.

Target Market(s)

Clients looking for legal services (professional)

Industry/Entity Type

Legal

Contact Information for Business Card

Doran Kelbrath
Partner
Mobile: 0461 738 524
Email: doran@kbtlaw.co
Website: www.kbtlaw.co
Level 3, 118 Wendmore Street
Sydney NSW 2000

Font styles to use
Other font styles liked:
• Avenir

Colors
f04a50
ffffff
1b1b1b

Requirements
Must have
• Black back with logo included in the centre of the card.
• Our font is Avenir.

```html
<!DOCTYPE html>
<html lang="en">
<head>
<meta charset="utf-8">
<title>KBT Legal Business Cards</title>
<link rel="stylesheet" href="https://fonts.googleapis.com/css2?family=Nunito+Sans:wght@400;600;700;800&display=swap">
<style>
  :root {
    --accent: #f04a50;
    --accent-deep: #d6244f;
    --white: #ffffff;
    --card: #1b1b1b;
    --stage: #121212;
    --emboss: #3b3b3b;
    --emboss-edge: #4a4a4a;
    --font: "Nunito Sans", "Avenir", sans-serif;
  }
  * { margin: 0; padding: 0; box-sizing: border-box; }
  html, body {
    width: 1200px;
    height: 900px;
    overflow: hidden;
    background: var(--stage);
    font-family: var(--font);
  }
  .canvas {
    position: relative;
    width: 1200px;
    height: 900px;
    display: flex;
    flex-direction: column;
    align-items: center;
    justify-content: center;
    gap: 40px;
  }
  .card {
    position: relative;
    width: 630px;
    height: 360px;
    background: var(--card);
    box-shadow: 0 18px 40px rgba(0,0,0,0.55);
  }

  /* Back side */
  .card-back {
    display: flex;
    align-items: center;
    justify-content: center;
  }
  .brand {
    display: flex;
    align-items: center;
    gap: 18px;
  }
  .brand-mark {
    width: 46px;
    height: 46px;
  }
  .brand-name {
    font-weight: 800;
    font-size: 40px;
    letter-spacing: 1px;
    line-height: 1;
  }
  .card-back .brand-mark { background: var(--emboss); }
  .card-back .brand-name {
    color: var(--emboss);
    text-shadow: 0 1px 0 var(--emboss-edge);
  }

  /* Front side */
  .card-front {
    display: grid;
    grid-template-columns: 300px 1fr;
    align-items: center;
    padding: 0 40px 0 50px;
  }
  .card-front .brand-mark { background: var(--accent-deep); }
  .card-front .brand-name { color: var(--white); }
  .contact {
    border-left: 2px solid var(--accent-deep);
    padding: 6px 0 6px 26px;
    color: var(--white);
  }
  .contact-name {
    color: var(--accent-deep);
    font-weight: 700;
    font-size: 24px;
    letter-spacing: 0.5px;
    text-transform: uppercase;
    line-height: 1.05;
  }
  .contact-title {
    font-size: 16px;
    font-weight: 400;
    margin-bottom: 14px;
  }
  .contact-address {
    font-size: 16px;
    line-height: 1.4;
    margin-bottom: 12px;
  }
  .contact-list { list-style: none; }
  .contact-list li {
    display: flex;
    align-items: center;
    gap: 10px;
    font-size: 16px;
    line-height: 1.5;
  }
  .contact-icon {
    width: 13px;
    height: 13px;
    flex: none;
  }
</style>
</head>
<body>
<main class="canvas">

  <section class="card card-back" aria-label="Card back">
    <div class="brand">
      <span class="brand-mark"></span>
      <span class="brand-name">KBT LEGAL</span>
    </div>
  </section>

  <section class="card card-front" aria-label="Card front">
    <div class="brand">
      <span class="brand-mark"></span>
      <span class="brand-name">KBT LEGAL</span>
    </div>
    <div class="contact">
      <h1 class="contact-name">Doran Kelbrath</h1>
      <p class="contact-title">General Manager</p>
      <p class="contact-address">Level 3, 118 Wendmore Street<br>Sydney NSW 2000</p>
      <ul class="contact-list">
        <li>
          <svg class="contact-icon" viewBox="0 0 16 16" aria-hidden="true">
            <path d="M4 1.5l2.4 3-1.3 1.6c.9 1.9 2.3 3.3 4.2 4.2l1.6-1.3 3 2.4-1.4 2.6C7 13.4 2.6 9 1.5 3z" fill="none" stroke="#d6244f" stroke-width="1.4" stroke-linejoin="round"/>
          </svg>
          0461 738 524
        </li>
        <li>
          <svg class="contact-icon" viewBox="0 0 16 16" aria-hidden="true">
            <rect x="1.5" y="3.5" width="13" height="9" fill="none" stroke="#d6244f" stroke-width="1.4"/>
            <path d="M1.5 3.5L8 9l6.5-5.5" fill="none" stroke="#d6244f" stroke-width="1.4"/>
          </svg>
          doran@kbtlaw.co
        </li>
        <li>
          <svg class="contact-icon" viewBox="0 0 16 16" aria-hidden="true">
            <circle cx="8" cy="8" r="6.5" fill="none" stroke="#d6244f" stroke-width="1.3"/>
            <ellipse cx="8" cy="8" rx="3" ry="6.5" fill="none" stroke="#d6244f" stroke-width="1.1"/>
            <path d="M1.5 8h13M2.5 4.8h11M2.5 11.2h11" stroke="#d6244f" stroke-width="1.1"/>
          </svg>
          www.kbtlaw.co
        </li>
      </ul>
    </div>
  </section>

</main>
</body>
</html>
```